Corbell Lending Partners - Real estate loans - need a business card with a logo

I need a logo and a business card that looks elegant - that looks as if it is a big stablish corporation - We do real estate loans, my goal is to brand myself with colors black background - gold or silver letters - some combination - Name of the company different color than the rest of the card -

```html
<!DOCTYPE html>
<html lang="en">
<head>
<meta charset="utf-8">
<title>Corbell Lending Partners — Business Card</title>
<link rel="stylesheet" href="https://fonts.googleapis.com/css2?family=Montserrat:wght@700;800&family=Arimo:wght@400&display=swap">
<style>
  :root {
    --backdrop: #1c1c1c;
    --gold: #cdb283;
    --gold-light: #d6bd8e;
    --gold-deep: #c4a775;
    --navy: #1d2c48;
    --navy-light: #243556;
    --white: #ffffff;
  }
  * { margin: 0; padding: 0; box-sizing: border-box; }
  html, body {
    width: 1200px; height: 900px; overflow: hidden;
    background: var(--backdrop);
  }
  .stage { position: relative; width: 1200px; height: 900px; }
  .card {
    position: absolute; left: 250px; width: 700px; height: 400px;
    box-shadow: 0 10px 30px rgba(0,0,0,0.5);
    overflow: hidden;
  }
  .card--front {
    top: 35px;
    background: linear-gradient(135deg, var(--gold-light), var(--gold-deep));
    display: flex; flex-direction: column; align-items: center; justify-content: center;
  }
  .card--back {
    top: 465px;
    background: linear-gradient(135deg, var(--navy), var(--navy-light));
  }
  .brand { display: flex; flex-direction: column; align-items: center; }
  .brand__mark { width: 78px; height: 78px; margin-bottom: 22px; }
  .brand__name {
    font-family: "Montserrat", sans-serif; font-weight: 800;
    text-transform: uppercase; text-align: center;
    line-height: 1.15; white-space: nowrap;
  }
  .card--front .brand__mark { background: var(--navy); }
  .card--front .brand__name { color: var(--navy); font-size: 34px; letter-spacing: 3px; }

  .back-brand {
    position: absolute; left: 40px; top: 0; width: 290px; height: 400px;
    display: flex; align-items: center; justify-content: center;
  }
  .card--back .brand__mark { width: 64px; height: 64px; margin-bottom: 20px; background: var(--white); }
  .card--back .brand__name { color: var(--white); font-size: 20px; letter-spacing: 1.5px; }

  .divider {
    position: absolute; left: 356px; top: 100px; width: 2px; height: 200px;
    background: var(--gold);
  }
  .contact {
    position: absolute; left: 388px; right: 36px; top: 100px;
    font-family: "Arimo", sans-serif; color: var(--white);
  }
  .contact__name {
    font-family: "Montserrat", sans-serif; font-weight: 700;
    color: var(--gold); font-size: 23px; letter-spacing: 0.5px;
    text-transform: uppercase; white-space: nowrap;
  }
  .contact__title { font-size: 17px; margin-top: 2px; }
  .contact__address { font-size: 17px; line-height: 1.35; margin-top: 16px; }
  .contact__list { list-style: none; margin-top: 10px; font-size: 17px; line-height: 1.45; }
  .contact__list li { display: flex; align-items: center; gap: 8px; white-space: nowrap; }
  .contact__icon { width: 12px; height: 12px; flex: none; }
</style>
</head>
<body>
<main class="stage">
  <section class="card card--front">
    <div class="brand">
      <span class="brand__mark"></span>
      <h1 class="brand__name">Corbell Lending<br>Partners</h1>
    </div>
  </section>

  <section class="card card--back">
    <div class="back-brand">
      <div class="brand">
        <span class="brand__mark"></span>
        <p class="brand__name">Corbell Lending<br>Partners</p>
      </div>
    </div>
    <span class="divider"></span>
    <div class="contact">
      <h2 class="contact__name">Daniel Whitaker</h2>
      <p class="contact__title">Founder</p>
      <p class="contact__address">418 Harlow Avenue<br>Marston, WA 99120</p>
      <ul class="contact__list">
        <li>
          <svg class="contact__icon" viewBox="0 0 12 12"><path d="M3 1 L5 3.5 L4 5 Q5 7 7 8 L8.5 7 L11 9 L10 11 Q4 11 1 3 Z" fill="#cdb283"/></svg>
          555 214 3086
        </li>
        <li>
          <svg class="contact__icon" viewBox="0 0 12 12"><rect x="1" y="2.5" width="10" height="7" fill="none" stroke="#cdb283" stroke-width="1.2"/><path d="M1 2.5 L6 6.5 L11 2.5" fill="none" stroke="#cdb283" stroke-width="1.2"/></svg>
          info@corbelllending.com
        </li>
        <li>
          <svg class="contact__icon" viewBox="0 0 12 12"><g fill="none" stroke="#cdb283" stroke-width="1"><circle cx="6" cy="6" r="5"/><ellipse cx="6" cy="6" rx="2.2" ry="5"/><path d="M1 6 H11 M2 3.5 H10 M2 8.5 H10"/></g></svg>
          www.corbelllending.com
        </li>
      </ul>
    </div>
  </section>
</main>
</body>
</html>
```